New Corporate Email Signature with Custom GIF KAV Electric LLC & KAV Fire & Security

Project Overview
KAV Electric LLC and KAV Fire & Security are seeking a professional, polished, and technically robust corporate email signature design. The project has two integrated deliverables:
A custom animated GIF representing both sides of our business
A complete corporate email signature layout designed for real-world compatibility (Gmail, Outlook, iOS, Android)
Our brand aesthetic is corporate, conservative, and clean. We value clarity, trust, professionalism, and subtle creativity β€” nothing overly flashy or cartoonish.
This design will be used across the entire company and must be visually aligned with our brand while remaining technically dependable.

PART 1 β€” Animated GIF Requirements
The GIF will be the core visual anchor of the new signature.
It must be clean, smooth, subtle, and optimized for email use.
βš™ Technical Requirements
Max file size: 150–200 KB (smaller is better)
Dimensions: approx 300px width (flexible, but must look good small)
Looping: continuous loop
Style: professional, minimalistic transitions

No rapid flashing or harsh animations
Must export cleanly into a format email clients accept

🎞 GIF Animation Sequence
Phase 1 β€” KAV Electric (KE)
Use the yellow β€œKE” avatar logo (provided).
Animation flow:
KE avatar appears
Full name β€œKAV Electric LLC” slides in, fades in, or otherwise appears smoothly
A scrolling or cycling list of service offerings displays:
EV Charging Stations
Generator & Transformers
Testing & Troubleshooting
LED Lighting Upgrades
After the list is shown, the entire KE segment fades out

Phase 2 β€” KAV Fire & Security (KF)
Use the red β€œKF” avatar logo (provided).
Animation flow mirrors Phase 1:
KF avatar appears
Full name β€œKAV Fire & Security” slides/fades in
Scrolling or cycling list of services displays:
Fire Alarm Upgrades
BQTL 48 Test & Inspect
Security Surveillance Systems
Access Control Systems
Data & Fiber Optic Cabling
Fade out β†’ loop back to KE
Creative Direction

Designers are encouraged to use:
Clean transitions
Soft fades
Professional typography
Modern minimalism
Consistent brand colors
High clarity at small sizes

Avoid:
Busy motion
Hard flashes
Excessive text overlays
Overly long transitions

The goal: a smooth, corporate-grade rotation that fits seamlessly into an email signature.

PART 2 β€” Corporate Email Signature Design

The signature must be visually appealing, brand-aligned, and structurally bulletproof across all major email systems.
πŸ“ Required Elements
πŸ‘€ Left Side Content
Circular headshot (we will supply final photos)
Social media icons with embedded URLs:
Facebook
LinkedIn
Google Business Profile
Instagram

Icons should be clean, modern, and in alignment with brand colors
πŸ“„ Right Side Content
Name
Title
KAV Electric LLC / KAV Fire & Security (depending on user)
Phone number
Email address
License# 52804
Physical office address: 384 Pembrook St, Alderton PA 07912

Small CTA for newsletter signup (button or micro-banner)

🏒 Branding Assets Provided

You will receive:
KE avatar logo
KF avatar logo
Full-name KE logo
Full-name KF logo

These should be incorporated naturally and professionally.

Design Requirements

Conservative corporate styling

Clean typography

Balanced use of white space

Professional hierarchy

Light and dark mode compatibility preferred

Layout should not rely on one large image

All images should export cleanly for hosting on servers/CDN

Avoid overly tall signatures

The final signature must present as modern, trustworthy, and technically reliable across platforms.

πŸ§ͺ Compatibility Requirements

The signature must display correctly in:

Gmail (web and mobile)

Outlook (desktop & online)

Apple Mail

iPhone Mail

Android mail apps

Designers must avoid DIV-based layouts and instead propose a layout that can be implemented using table-based HTML, which is the industry standard for email compatibility.

You do not need to build the HTML β€” only supply the final layered design (PSD/AI/Figma) plus a clear structural layout that can be converted to HTML later.

πŸ“¦ Deliverables
1. Animated GIF

Final optimized GIF

Source file (After Effects, Photoshop, or equivalent)

Export guidelines so we can reproduce future versions

2. Email Signature Design

Full static design mockup

Modular layout for each employee

Icon set for social media

Newsletter CTA element

Clear spacing, alignment, and typography specifications

All source files (PSD, AI, Figma, etc.)

🧭 Creative Guidance Summary

We want:
βœ” Modern
βœ” Corporate
βœ” Minimalistic
βœ” Professional
βœ” Clean motion
βœ” Consistent branding
βœ” Email-safe elements

We do not want:
✘ Flashy marketing look
✘ Overly colorful or playful styles
✘ Hard-to-read fonts
✘ Heavy animation
✘ Oversized signatures

πŸ›  Tools & Format Flexibility

We allow full creative freedom regarding:

Animation style

Typography choices

Structuring of the two-column layout

How the service lists scroll or cycle

As long as the end result is clean, brand-aligned, professional, and email-compatible.

πŸ’¬ Final Note to Designers

We encourage creativity within the boundaries of corporate professionalism.
This signature will represent our company every time an email is sent β€” it must communicate trust, clarity, expertise, and brand strength.

```html
<!DOCTYPE html>
<html lang="en">
<head>
<meta charset="utf-8">
<title>KAV Electric LLC – Email Signature</title>
<link href="https://fonts.googleapis.com/css2?family=Poppins:wght@400;500;600;700&display=swap" rel="stylesheet">
<style>
  :root {
    --brand-yellow: #e9c912;
    --brand-yellow-soft: #f2dc4a;
    --ink-grey: #5b5b5b;
    --text-dark: #2f2f2f;
    --icon-bg: #8c8a7e;
    --paper: #ffffff;
  }
  html, body {
    margin: 0;
    padding: 0;
    overflow: hidden;
    background: var(--paper);
  }
  .signature {
    position: relative;
    width: 1200px;
    height: 400px;
    overflow: hidden;
    background: var(--paper);
    font-family: "Poppins", sans-serif;
  }
  .accent-band {
    position: absolute;
    inset: 0;
  }
  .headshot {
    position: absolute;
    left: 86px;
    top: 6px;
    width: 300px;
    height: 300px;
    border-radius: 50%;
    border: 8px solid var(--paper);
    background: radial-gradient(circle at 50% 40%, #9a9a98 0%, #5d5f63 55%, #2e3440 100%);
    box-shadow: 0 2px 6px rgba(0,0,0,0.12);
  }
  .social-links {
    position: absolute;
    left: 114px;
    top: 344px;
    display: flex;
    gap: 24px;
  }
  .social-links span {
    display: block;
    width: 44px;
    height: 44px;
    border-radius: 50%;
    border: 4px solid var(--ink-grey);
    box-sizing: border-box;
  }
  .details {
    position: absolute;
    left: 510px;
    top: 16px;
  }
  .person-name {
    margin: 0;
    font-size: 38px;
    font-weight: 700;
    line-height: 1.2;
    color: var(--ink-grey);
    letter-spacing: 0.5px;
  }
  .person-name .first-name { color: var(--brand-yellow); }
  .company-name {
    margin: 8px 0 0;
    font-size: 26px;
    font-weight: 600;
    line-height: 1.2;
    letter-spacing: 1px;
    color: var(--ink-grey);
    text-transform: uppercase;
  }
  .contact-list {
    list-style: none;
    margin: 4px 0 0;
    padding: 0;
  }
  .contact-list li {
    display: flex;
    align-items: center;
    height: 53px;
    font-size: 24px;
    color: var(--text-dark);
  }
  .contact-list svg {
    width: 40px;
    height: 40px;
    margin-right: 14px;
    margin-left: 6px;
    flex: none;
  }
  .cta-button {
    position: absolute;
    left: 524px;
    top: 340px;
    width: 264px;
    height: 36px;
    border-radius: 18px;
    background: var(--brand-yellow);
    color: var(--text-dark);
    font-size: 24px;
    font-weight: 500;
    line-height: 36px;
    text-align: center;
    text-decoration: none;
  }
</style>
</head>
<body>
<div class="signature">
  <svg class="accent-band" width="1200" height="400" viewBox="0 0 1200 400" aria-hidden="true">
    <polygon points="0,60 470,400 0,400" fill="var(--brand-yellow)"/>
    <polygon points="0,0 130,0 0,70" fill="var(--brand-yellow-soft)"/>
  </svg>

  <div class="headshot" role="img" aria-label="Circular headshot of the employee"></div>

  <nav class="social-links" aria-label="Social profiles">
    <span aria-label="Social profile one"></span>
    <span aria-label="Social profile two"></span>
    <span aria-label="Social profile three"></span>
    <span aria-label="Social profile four"></span>
  </nav>

  <section class="details">
    <h1 class="person-name"><span class="first-name">Daniel</span> Mercer</h1>
    <p class="company-name">KAV Electric LLC</p>
    <ul class="contact-list">
      <li>
        <svg viewBox="0 0 40 40" aria-hidden="true">
          <circle cx="20" cy="20" r="20" fill="var(--icon-bg)"/>
          <path d="M14 11c1-1 2-1 3 0l2 3c.6 1 .4 2-.4 2.7l-1 .8c.8 2 2.6 3.8 4.6 4.6l.8-1c.7-.8 1.7-1 2.7-.4l3 2c1 1 1 2 0 3l-1.4 1.4c-1.2 1.2-3 1.4-4.6.6-4-2-7.4-5.4-9.4-9.4-.8-1.6-.6-3.4.6-4.6z" fill="var(--brand-yellow)"/>
        </svg>
        +1555 555 0142
      </li>
      <li>
        <svg viewBox="0 0 40 40" aria-hidden="true">
          <circle cx="20" cy="20" r="20" fill="var(--icon-bg)"/>
          <rect x="10" y="13" width="20" height="14" rx="2" fill="var(--brand-yellow)"/>
          <path d="M10.5 14l9.5 7 9.5-7" fill="none" stroke="var(--icon-bg)" stroke-width="1.8"/>
        </svg>
        kavelectric@daniel.com
      </li>
      <li>
        <svg viewBox="0 0 40 40" aria-hidden="true">
          <circle cx="20" cy="20" r="20" fill="var(--icon-bg)"/>
          <rect x="9" y="12" width="22" height="16" rx="2" fill="none" stroke="var(--brand-yellow)" stroke-width="2"/>
          <circle cx="15.5" cy="18.5" r="2.5" fill="var(--brand-yellow)"/>
          <path d="M11.5 25c.5-2.5 2-3.5 4-3.5s3.5 1 4 3.5z" fill="var(--brand-yellow)"/>
          <path d="M22 17h6M22 21h6M22 25h4" stroke="var(--brand-yellow)" stroke-width="1.8"/>
        </svg>
        License# 52804
      </li>
      <li>
        <svg viewBox="0 0 40 40" aria-hidden="true">
          <circle cx="20" cy="20" r="20" fill="var(--icon-bg)"/>
          <path d="M20 9c-4.4 0-8 3.4-8 7.8 0 5.6 8 14.2 8 14.2s8-8.6 8-14.2C28 12.4 24.4 9 20 9z" fill="var(--brand-yellow)"/>
          <circle cx="20" cy="17" r="3" fill="var(--icon-bg)"/>
        </svg>
        384 Pembrook St, Alderton PA 07912
      </li>
    </ul>
  </section>

  <a class="cta-button" href="#newsletter">Stay Connected</a>
</div>
</body>
</html>
```